I would like a business card to match my truck wrap and logo. I would like the font to match my existing business card please.

Industry/Entity Type

Painter

Contact Information for Business Card

Rodrigo Fenwar 801-437-2190 Fenwarcoatings.utah@brelmox.com
SERVICES - Custom Paint & Stain, Interior & Exterior, Epoxy Coatings / Garage Floors, Cabinet Refinishing, Log Staining and Refinishing.

Requirements
Nice to have
• I would like to have the white and grey line like the bottom of my vehicle wrap, Light Grey to match my truck also.

```html
<!DOCTYPE html>
<html lang="en">
<head>
<meta charset="UTF-8">
<title>Fenwar Coatings – Business Card</title>
<link href="https://fonts.googleapis.com/css2?family=Montserrat:wght@400;500;800&family=Oswald:wght@600&display=swap" rel="stylesheet">
<style>
  :root {
    --backdrop: #b1b1ac;
    --card: #2b2b2c;
    --accent: #14a4e6;
    --text: #f2f2f2;
    --divider: #4a4a4c;
  }
  * { box-sizing: border-box; margin: 0; padding: 0; }
  html, body { width: 1200px; height: 801px; overflow: hidden; }
  body {
    background: var(--backdrop);
    font-family: "Montserrat", sans-serif;
    position: relative;
  }
  .card {
    position: absolute;
    top: 240px;
    width: 560px;
    height: 320px;
    background: var(--card);
    border-bottom: 5px solid var(--accent);
    box-shadow: 0 10px 24px rgba(0,0,0,.25);
    color: var(--text);
  }
  .card--front { left: 27px; }
  .card--back { left: 613px; }

  .brand {
    display: flex;
    align-items: center;
    gap: 12px;
    font-family: "Montserrat", sans-serif;
    font-weight: 800;
    color: var(--accent);
    letter-spacing: 1px;
    white-space: nowrap;
  }
  .brand__square { display: block; background: var(--accent); }

  .card--front .brand { position: absolute; left: 50%; top: 74px; transform: translateX(-50%); font-size: 30px; }
  .card--front .brand__square { width: 34px; height: 34px; }

  .details {
    position: absolute;
    left: 24px;
    right: 24px;
    bottom: 58px;
    display: flex;
    justify-content: center;
    align-items: stretch;
    gap: 16px;
  }
  .holder {
    display: flex;
    flex-direction: column;
    justify-content: flex-end;
    text-align: right;
    white-space: nowrap;
  }
  .holder__name {
    font-family: "Oswald", sans-serif;
    font-weight: 600;
    font-size: 30px;
    color: var(--accent);
    text-transform: uppercase;
    line-height: 1;
    letter-spacing: .5px;
  }
  .holder__title { font-size: 13px; font-weight: 500; margin-top: 5px; }

  .divider { width: 1px; background: var(--divider); flex: none; }

  .contact { list-style: none; font-size: 12px; line-height: 1.75; white-space: nowrap; }
  .contact li { display: flex; align-items: center; gap: 7px; }
  .contact svg { width: 10px; height: 10px; flex: none; }

  .card--back .brand { position: absolute; left: 50%; top: 88px; transform: translateX(-50%); font-size: 38px; }
  .card--back .brand__square { width: 44px; height: 44px; }

  .services { position: absolute; left: 0; right: 0; top: 190px; text-align: center; }
  .services__heading { color: var(--accent); font-size: 20px; font-weight: 500; letter-spacing: 1px; }
  .services__list { font-size: 13.5px; line-height: 1.55; margin-top: 4px; }
  .services__sep { color: var(--accent); padding: 0 3px; }
</style>
</head>
<body>

<section class="card card--front">
  <div class="brand"><span class="brand__square"></span>FENWAR COATINGS</div>

  <div class="details">
    <div class="holder">
      <p class="holder__name">Rodrigo Fenwar</p>
      <p class="holder__title">Director</p>
    </div>

    <span class="divider"></span>

    <ul class="contact">
      <li>
        <svg viewBox="0 0 10 10"><path d="M2 1l2 2-1 1.3a6 6 0 0 0 2.7 2.7L7 6l2 2-1.3 1.3C4.5 9 1 5.5.7 2.3z" fill="#f2f2f2"/></svg>
        801-437-2190
      </li>
      <li>
        <svg viewBox="0 0 10 10"><rect x=".7" y="2" width="8.6" height="6" fill="none" stroke="#f2f2f2" stroke-width="1"/><path d="M.7 2L5 5.5 9.3 2" fill="none" stroke="#f2f2f2" stroke-width="1"/></svg>
        Fenwarcoatings.utah@brelmox.com
      </li>
      <li>
        <svg viewBox="0 0 10 10"><circle cx="5" cy="5" r="4.3" fill="none" stroke="#f2f2f2"/><path d="M.7 5h8.6M5 .7c-2.5 2.6-2.5 6 0 8.6M5 .7c2.5 2.6 2.5 6 0 8.6" fill="none" stroke="#f2f2f2" stroke-width=".8"/></svg>
        www.fenwarcoatings-utah.com
      </li>
    </ul>
  </div>
</section>

<section class="card card--back">
  <div class="brand"><span class="brand__square"></span>FENWAR COATINGS</div>

  <div class="services">
    <h2 class="services__heading">SERVICES</h2>
    <p class="services__list">
      Custom Paint &amp; Stain<span class="services__sep">|</span>Interior &amp; Exterior<span class="services__sep">|</span>Epoxy Coatings / Garage Floors<br>
      Cabinet Refinishing<span class="services__sep">|</span>Log Staining and Refinishing.
    </p>
  </div>
</section>

</body>
</html>
```